BrimTaps.com

Hey guys!

We are looking for an innovative 1 page web design for our PPC network website - http://quillpeekshot.example/4k82vmtq7r
We are a PPC social media start up, which works with many social media publishers worldwide.
The design must be clean, flat, trendy, we would like to keep our 1 page design structure, but add your own personal touch-up.

We would like you to make it look like a Million $ company.

Good luck!

Target Market(s)

Big Internet Advertising Companies

Number of Pages Required

1 page

```html
<!DOCTYPE html>
<html lang="en">
<head>
<meta charset="utf-8">
<title>BrimTaps.com</title>
<link href="https://fonts.googleapis.com/css2?family=Open+Sans:wght@400;600;700&display=swap" rel="stylesheet">
<style>
:root{
  --ink:#222;
  --muted:#666;
  --cyan:#17b4e8;
  --cyan-dark:#0e9bd0;
  --green:#2eae4a;
  --night:#0d1116;
  --night-2:#1a2430;
  --grey-band:#f0f0f0;
  --white:#fff;
  --line:#d8d8d8;
}
*{box-sizing:border-box;margin:0;padding:0}
html,body{width:1200px;height:2796px;overflow:hidden}
body{font-family:"Open Sans",Arial,sans-serif;color:var(--ink);background:var(--white);position:relative}
.wrap{width:840px;margin:0 auto;position:relative}
.btn{display:inline-block;background:var(--cyan);color:var(--white);font-weight:700;font-size:16px;text-transform:uppercase;padding:10px 26px;letter-spacing:.5px}
h2.section-title{text-align:center;font-size:22px;font-weight:700;text-transform:uppercase;letter-spacing:.5px}
.subtitle{text-align:center;color:var(--muted);font-size:15px;margin-top:14px}

/* hero */
.hero{height:660px;background:radial-gradient(ellipse at 60% 40%,#3a4a5a 0%,#1c2632 45%,#0b0f14 100%);position:relative;color:var(--white)}
.topbar{height:80px;display:flex;align-items:center;justify-content:space-between;padding:0 30px}
.brand{display:flex;align-items:center;gap:14px;font-size:38px;font-weight:700;color:var(--white)}
.brand-dot{width:46px;height:46px;border-radius:50%;background:var(--white)}
.nav{display:flex;gap:28px;font-size:13px;font-weight:700;text-transform:uppercase}
.cyan-strip{height:10px;background:var(--cyan)}
.account{position:absolute;right:40px;top:100px;display:flex;gap:12px}
.account span{background:var(--cyan);font-size:12px;font-weight:700;padding:5px 16px;text-transform:uppercase}
.devices{position:absolute;left:300px;top:140px;width:600px;height:350px;border-radius:8px;background:linear-gradient(160deg,#e8edf1,#9aa6b0)}
.tagline{position:absolute;left:330px;top:520px;width:540px;height:44px;background:#000;display:flex;align-items:center;justify-content:center;font-size:20px;font-weight:700;text-transform:uppercase}
.hero .btn{position:absolute;left:520px;top:590px;background:var(--green)}

/* publisher */
.publisher{height:388px;padding-top:52px}
.perks{position:absolute;left:0;top:70px;list-style:none}
.perks li{font-size:17px;font-weight:600;margin-bottom:26px;display:flex;align-items:center;gap:16px}
.perks svg{width:22px;height:16px}
.publisher .btn{position:absolute;left:0;top:262px;font-size:14px}
.join-visual{position:absolute;right:0;top:62px;width:300px;height:220px;border-radius:4px;background:linear-gradient(165deg,#4fcf62 0%,#2a9a3f 55%,#3a3f44 100%)}

/* advertise */
.advertise{height:352px;background:var(--grey-band);padding-top:36px}
.adv-grid{display:flex;justify-content:space-between;margin-top:40px}
.adv-item{width:180px;text-align:center}
.circle{width:120px;height:120px;border-radius:50%;background:var(--cyan);margin:0 auto 20px;display:flex;align-items:center;justify-content:center}
.adv-item p{font-size:14px;font-weight:700;line-height:1.45}

/* how it works */
.how{height:240px;padding-top:50px;text-align:center}
.how p{font-size:14px;color:var(--muted);line-height:1.5;margin:20px auto 0;width:720px}
.how .btn{margin-top:22px;font-size:14px}

/* automation */
.automation{height:380px;background:var(--grey-band);padding-top:54px}
.automation .lead{text-align:center;font-size:14px;color:var(--muted);line-height:1.5;width:720px;margin:16px auto 0}
.auto-cols{display:flex;margin-top:50px;border-top:1px solid var(--line)}
.auto-col{flex:1;padding:22px 18px 0;border-right:1px solid var(--line)}
.auto-col:last-child{border-right:0}
.auto-col h3{font-size:15px;font-weight:700;line-height:1.4}
.auto-col p{font-size:12px;color:var(--muted);margin-top:12px;line-height:1.5}

/* faq */
.faq{height:380px;padding-top:46px}
.faq-grid{display:grid;grid-template-columns:1fr 1fr;gap:44px 60px;margin-top:48px;width:720px;margin-left:auto;margin-right:auto}
.faq-item{display:flex;gap:18px;border-bottom:1px solid var(--line);padding-bottom:14px}
.faq-item b{color:var(--green);font-size:40px;line-height:1}
.faq-item p{font-size:15px;font-weight:700;line-height:1.4}

/* contact */
.contact{height:360px;background:var(--night);color:var(--white);padding-top:14px}
.contact h2.section-title{font-size:20px}
.contact-form{position:absolute;left:60px;top:70px;width:180px}
.contact-form div{background:var(--white);color:#555;font-size:12px;padding:5px 8px;margin-bottom:10px;height:26px}
.contact-form .msg{height:100px}
.contact-form .send{width:70px;background:#444;color:#ddd;text-align:center;height:26px}
.contact-info{position:absolute;left:420px;top:70px;width:260px;font-size:12px;color:#bbb;line-height:1.6}
.socials{display:flex;gap:6px;margin-top:20px}
.socials span{width:22px;height:22px;background:#555}
.footer{height:36px;background:#000;color:#aaa;font-size:12px;display:flex;align-items:center;justify-content:space-between;padding:0 120px}
</style>
</head>
<body>

<section class="hero">
  <header class="topbar">
    <div class="brand"><span class="brand-dot"></span>BrimTaps</div>
    <nav class="nav"><span>Publishers</span><span>Advertisers</span><span>How it works?</span><span>Automation</span><span>FAQ</span><span>Contact us</span></nav>
  </header>
  <div class="cyan-strip"></div>
  <div class="account"><span>Login</span><span>Signup</span></div>
  <div class="devices" role="img" aria-label="Desktop, tablet and phone showing the platform dashboard"></div>
  <div class="tagline">Get paid to share high quality</div>
  <span class="btn">Sign up now</span>
</section>

<section class="publisher">
  <h2 class="section-title">Become our publisher</h2>
  <div class="wrap">
    <ul class="perks">
      <li><svg viewBox="0 0 22 16"><path d="M0 5h12V0l10 8-10 8v-5H0z" fill="#2eae4a"/></svg>Premium Benefits</li>
      <li><svg viewBox="0 0 22 16"><path d="M0 5h12V0l10 8-10 8v-5H0z" fill="#2eae4a"/></svg>Detailed Reports</li>
      <li><svg viewBox="0 0 22 16"><path d="M0 5h12V0l10 8-10 8v-5H0z" fill="#2eae4a"/></svg>Dedicated Support</li>
      <li><svg viewBox="0 0 22 16"><path d="M0 5h12V0l10 8-10 8v-5H0z" fill="#2eae4a"/></svg>Social Power</li>
    </ul>
    <span class="btn">Join our team</span>
    <div class="join-visual" role="img" aria-label="Illustration of a desktop monitor inviting publishers to join for free"></div>
  </div>
</section>

<section class="advertise">
  <h2 class="section-title">Advertise on BrimTaps</h2>
  <p class="subtitle">The regular search engine PPC advertising is NOT working anymore.</p>
  <div class="wrap adv-grid">
    <div class="adv-item"><div class="circle"><svg width="50" height="50" viewBox="0 0 50 50" fill="none" stroke="#fff" stroke-width="4"><rect x="8" y="6" width="34" height="26"/><path d="M16 32l-6 14M34 32l6 14M25 32v10"/></svg></div><p>Proin gravida nibh vel velit auctor aliquet</p></div>
    <div class="adv-item"><div class="circle"><svg width="50" height="50" viewBox="0 0 50 50" fill="#fff"><circle cx="12" cy="25" r="7"/><circle cx="38" cy="11" r="7"/><circle cx="38" cy="39" r="7"/><path d="M12 25L38 11M12 25l26 14" stroke="#fff" stroke-width="4"/></svg></div><p>Proin gravida nibh vel velit auctor aliquet</p></div>
    <div class="adv-item"><div class="circle"><svg width="50" height="50" viewBox="0 0 50 50" fill="none" stroke="#fff" stroke-width="4"><rect x="6" y="6" width="38" height="38"/><path d="M12 36l10-10 6 6 12-14"/></svg></div><p>Proin gravida nibh vel velit auctor aliquet</p></div>
    <div class="adv-item"><div class="circle"><svg width="50" height="50" viewBox="0 0 50 50" fill="#fff"><path d="M20 6h10l12 38H8z"/><path d="M25 10v6M25 22v6M25 34v6" stroke="#17b4e8" stroke-width="3"/></svg></div><p>Proin gravida nibh vel velit auctor aliquet</p></div>
  </div>
</section>

<section class="how">
  <h2 class="section-title">How it works</h2>
  <p>Lorem ipsum non gravida nibh vel velit auctor aliquet. Aenean sollicitudin, lorem quis bibendum auctor, nisi elit consequat ipsum, nec sagittis sem nibh id elit. Duis sed odio sit amet nibh vulputate cursus a sit amet mauris.</p>
  <span class="btn">Sign up now</span>
</section>

<section class="automation">
  <h2 class="section-title">Automation</h2>
  <p class="lead">Lorem ipsum non gravida nibh vel velit auctor aliquet. Aenean sollicitudin, lorem quis bibendum auctor, nisi elit consequat ipsum, nec sagittis sem nibh id elit. Duis sed odio sit amet nibh.</p>
  <div class="wrap auto-cols">
    <div class="auto-col"><h3>Proin gravida nibh vel velit auctor aliquet</h3><p>Aenean sollicitudin, lorem quis bibendum auctor, nisi elit consequat ipsum nec sagittis sem.</p></div>
    <div class="auto-col"><h3>Proin gravida nibh vel velit auctor aliquet</h3><p>Aenean sollicitudin, lorem quis bibendum auctor, nisi elit consequat ipsum nec sagittis sem.</p></div>
    <div class="auto-col"><h3>Nibh vel velit auctor aliquet</h3><p>Aenean sollicitudin, lorem quis bibendum auctor, nisi elit consequat ipsum nec sagittis sem.</p></div>
  </div>
</section>

<section class="faq">
  <h2 class="section-title">FAQ</h2>
  <p class="subtitle">You've Got Questions, We've Got Answers</p>
  <div class="faq-grid">
    <div class="faq-item"><b>?</b><p>Gravida nibh vel velit auctor aliquet nisi elit consequat ipsum</p></div>
    <div class="faq-item"><b>?</b><p>Gravida nibh vel velit auctor aliquet nisi elit consequat ipsum</p></div>
    <div class="faq-item"><b>?</b><p>Gravida nibh vel velit auctor aliquet nisi elit consequat ipsum</p></div>
    <div class="faq-item"><b>?</b><p>Gravida nibh vel velit auctor aliquet nisi elit consequat ipsum</p></div>
  </div>
</section>

<section class="contact">
  <h2 class="section-title">Contact us</h2>
  <div class="wrap">
    <div class="contact-form">
      <div>Name</div>
      <div>Email</div>
      <div class="msg">Message</div>
      <div class="send">Send</div>
    </div>
    <div class="contact-info">
      <p>We make sharing simple for publishers. Reach our support team any time, day or night, for quick help.</p>
      <p style="margin-top:14px">Ph: +1 (555) 014-2290</p>
      <p>Email: hello@brimtaps.example</p>
      <div class="socials"><span></span><span></span><span></span><span></span><span></span><span></span></div>
    </div>
  </div>
</section>

<footer class="footer">
  <span>Copyright © 2013 BrimTaps Inc. All Rights Reserved. | Terms Of Service | Privacy Policy</span>
  <span>Top</span>
</footer>

</body>
</html>
```